Marlow Sail Works President Business Card Carbon fiber catamarans

Hi.. I need a new business card design.. I am the President of a high tech yacht builder. We build Carbon Fiber go fast catamarans... Maybe we use the file I am sharing to you as the back of the card.. We need to look cool and crisp ...

Target Market(s)

Affluent People who will purchase a cool yacht

Industry/Entity Type

Custom Yacht Builder

Contact Information for Business Card

Dean Pellway , President, 731.508.2164 USA

Font styles to use
Serif

Requirements
Must have
• the clean crisp cool feel
Nice to have
• clean and crisp
Should not have
• Bold ugly

```html
<!DOCTYPE html>
<html lang="en">
<head>
<meta charset="utf-8">
<title>Marlow Sail Works – Business Card</title>
<link rel="stylesheet" href="https://fonts.googleapis.com/css2?family=Arimo:ital,wght@0,400;0,700;1,400&display=swap">
<style>
  :root {
    --backdrop: #0d0d0e;
    --card: #2a2a2c;
    --card-edge: #4a4a4d;
    --silver: #d9d9dc;
    --silver-soft: #b9b9bd;
    --rule: #9a9a9e;
  }
  * { box-sizing: border-box; margin: 0; padding: 0; }
  html, body {
    width: 1200px; height: 963px; overflow: hidden;
    background: var(--backdrop);
    font-family: "Arimo", Arial, sans-serif;
  }
  .sheet {
    width: 1200px; height: 963px;
    display: flex; flex-direction: column;
    align-items: center; justify-content: center; gap: 56px;
  }
  .card {
    width: 700px; height: 400px;
    background: var(--card);
    border: 1px solid var(--card-edge);
    border-radius: 26px;
    box-shadow: 0 18px 40px rgba(0,0,0,.6);
    position: relative;
  }
  /* Back: brand mark */
  .card-back { display: flex; align-items: center; justify-content: center; gap: 22px; }
  .brand-dot {
    width: 58px; height: 58px; border-radius: 50%;
    background: var(--silver-soft);
  }
  .brand-name {
    color: var(--silver);
    font-weight: 400;
    font-size: 46px;
    letter-spacing: 8px;
    line-height: 1.05;
    text-transform: uppercase;
  }
  /* Front: contact details */
  .card-front { color: var(--silver); }
  .identity {
    position: absolute; right: 372px; top: 128px; text-align: right;
  }
  .person-name {
    font-weight: 700; font-style: italic; font-size: 25px;
    letter-spacing: .5px; text-transform: uppercase;
  }
  .person-role {
    font-style: italic; font-size: 18px; color: var(--silver-soft); margin-top: 2px;
  }
  .divider {
    position: absolute; left: 348px; top: 118px;
    width: 1px; height: 96px; background: var(--rule);
  }
  .contacts {
    position: absolute; left: 372px; top: 122px;
    list-style: none; font-size: 19px; line-height: 30px;
  }
  .contacts li { display: flex; align-items: center; gap: 10px; }
  .contacts svg { width: 16px; height: 16px; fill: var(--silver); flex: none; }
  .address {
    position: absolute; left: 0; right: 0; top: 262px;
    text-align: center; font-size: 18px; color: var(--silver-soft);
  }
</style>
</head>
<body>
<main class="sheet">
  <section class="card card-back" aria-label="Card back">
    <span class="brand-dot"></span>
    <span class="brand-name">Marlow<br>Sail Works</span>
  </section>

  <section class="card card-front" aria-label="Card front">
    <div class="identity">
      <p class="person-name">Dean Pellway</p>
      <p class="person-role">President</p>
    </div>
    <span class="divider"></span>
    <ul class="contacts">
      <li>
        <svg viewBox="0 0 16 16" aria-hidden="true"><path d="M3.2 1.5l2.3 2.6-1.3 1.7c.9 2 2.4 3.5 4.3 4.4l1.6-1.3 2.6 2.3-1.3 2.3C6.3 13.2 2.5 9.4 1 4.4z"/></svg>
        731.508.2164
      </li>
      <li>
        <svg viewBox="0 0 16 16" aria-hidden="true"><path d="M1 3h14v10H1zm1.4 1.2L8 8.6l5.6-4.4zM2 5.4V12h12V5.4L8 10z"/></svg>
        dean@marlowsail.com
      </li>
      <li>
        <svg viewBox="0 0 16 16" aria-hidden="true"><path d="M8 1a7 7 0 100 14A7 7 0 008 1zm0 1.5c.9 0 1.8 1.9 2.1 4.5H5.9C6.2 4.4 7.1 2.5 8 2.5zM2.6 7h2c.1-1.6.4-3 .9-4A5.5 5.5 0 002.6 7zm8.8 0h2a5.5 5.5 0 00-2.9-4c.5 1 .8 2.4.9 4zM2.6 9a5.5 5.5 0 002.9 4c-.5-1-.8-2.4-.9-4zm3.3 0c.3 2.6 1.2 4.5 2.1 4.5s1.8-1.9 2.1-4.5zm5.5 0c-.1 1.6-.4 3-.9 4a5.5 5.5 0 002.9-4z"/></svg>
        www.marlowsail.com
      </li>
    </ul>
    <p class="address">Your address, city, state, ZIP 0000</p>
  </section>
</main>
</body>
</html>
```